Vantiqo custom business card design

Need a authentic, innovative business card design for a new mobile app business. I am uploading a few screen images from our app for you to view. I would like app design theme to match business card design. I can also send logo images.

```html
<!DOCTYPE html>
<html lang="en">
<head>
<meta charset="utf-8">
<title>Vantiqo Business Card</title>
<link href="https://fonts.googleapis.com/css2?family=Work+Sans:wght@400;500;800&display=swap" rel="stylesheet">
<style>
  :root {
    --stage: #2a2a2c;
    --card: #262628;
    --card-back: #1f1f21;
    --purple: #6a2f96;
    --white: #f2f2f2;
    --emboss: #3a3a3d;
  }
  html, body {
    margin: 0;
    padding: 0;
    width: 1200px;
    height: 900px;
    overflow: hidden;
    background: var(--stage);
    font-family: "Work Sans", sans-serif;
  }
  .canvas {
    position: relative;
    width: 1200px;
    height: 900px;
  }
  .card {
    position: absolute;
    left: 285px;
    width: 630px;
    height: 360px;
    border-radius: 4px;
    box-shadow: 0 10px 30px rgba(0,0,0,0.45);
    overflow: hidden;
  }
  .card-back { top: 60px; background: var(--card-back); }
  .card-front { top: 470px; background: var(--card); }

  .back-pattern {
    position: absolute;
    inset: 0;
    background: linear-gradient(120deg, var(--card-back) 0%, var(--emboss) 100%);
  }
  .back-center-dot {
    position: absolute;
    left: 300px;
    top: 165px;
    width: 30px;
    height: 30px;
    border-radius: 50%;
    background: var(--purple);
  }

  .brand-name {
    position: absolute;
    left: 40px;
    top: 28px;
    margin: 0;
    font-size: 50px;
    font-weight: 800;
    line-height: 1.1;
    color: var(--purple);
    letter-spacing: -0.5px;
  }
  .tagline {
    position: absolute;
    left: 40px;
    top: 100px;
    margin: 0;
    width: 300px;
    font-size: 15px;
    line-height: 1.3;
    color: var(--white);
  }
  .person {
    position: absolute;
    left: 40px;
    top: 172px;
  }
  .person-name {
    margin: 0;
    font-size: 23px;
    font-weight: 500;
    color: var(--purple);
    text-transform: uppercase;
    letter-spacing: 0.5px;
  }
  .person-role {
    margin: 2px 0 0;
    font-size: 18px;
    color: var(--white);
  }
  .contacts {
    position: absolute;
    left: 40px;
    top: 252px;
    margin: 0;
    padding: 0;
    list-style: none;
  }
  .contacts li {
    display: flex;
    align-items: center;
    gap: 12px;
    font-size: 17px;
    color: var(--white);
    height: 28px;
  }
  .contacts svg { width: 14px; height: 14px; flex: none; }

  .mark {
    position: absolute;
    left: 375px;
    top: 55px;
    width: 220px;
    display: flex;
    flex-direction: column;
    align-items: center;
    gap: 18px;
  }
  .mark-circle {
    width: 180px;
    height: 180px;
    border-radius: 50%;
    background: var(--purple);
  }
  .mark-name {
    font-size: 36px;
    font-weight: 800;
    color: var(--purple);
  }
</style>
</head>
<body>
<main class="canvas">
  <section class="card card-back">
    <div class="back-pattern" role="img" aria-label="Repeating embossed brand pattern across the card back"></div>
    <div class="back-center-dot"></div>
  </section>

  <section class="card card-front">
    <h1 class="brand-name">Vantiqo</h1>
    <p class="tagline">A Creative &amp; Connected Knowledge Sharing Network</p>

    <div class="person">
      <p class="person-name">Marcus Ellery</p>
      <p class="person-role">COO/Co-founder</p>
    </div>

    <ul class="contacts">
      <li>
        <svg viewBox="0 0 16 16"><path d="M4 1 L6.5 4 L5 6 Q6.5 9.5 10 11 L12 9.5 L15 12 L13 15 Q3 13 1 3 Z" fill="#6a2f96"/></svg>
        555 018 2746
      </li>
      <li>
        <svg viewBox="0 0 16 16"><rect x="1" y="3" width="14" height="10" fill="none" stroke="#6a2f96" stroke-width="1.5"/><path d="M1 3 L8 9 L15 3" fill="none" stroke="#6a2f96" stroke-width="1.5"/></svg>
        marcus.ellery@vantiqoapp.com
      </li>
      <li>
        <svg viewBox="0 0 16 16"><circle cx="8" cy="8" r="7" fill="none" stroke="#6a2f96" stroke-width="1.5"/><ellipse cx="8" cy="8" rx="3" ry="7" fill="none" stroke="#6a2f96" stroke-width="1.2"/><path d="M1 8 H15" stroke="#6a2f96" stroke-width="1.2"/></svg>
        www.vantiqoapp.com
      </li>
    </ul>

    <div class="mark">
      <div class="mark-circle"></div>
      <span class="mark-name">Vantiqo</span>
    </div>
  </section>
</main>
</body>
</html>
```